Brookvale Building Company - advertisement poster

I am looking to print some canvas signs to advertise my general contracting company, Brookvale Building Company. The sign will measure 6' long x 3' high so the size should match that ratio. I already have a logo icon, which is the Letter 'B' and some trees that I would like to incorporate, see attached. I would also like the to have the following information listed:
1) phone number: 831-555-0172
2) email: brookvalebuildingcompany@mailnest.example
3) website: brookvalebuildingcompany.example
4) Lic#4826130
5) I want to use this text: "BUILD WITH THE B-CREW!"

The ad should be relatively simple and clean. Black and Green are my company colors. I am open to creative ideas!

Target Market(s)

People looking to renovate their homes

Industry/Entity Type

Construction

Colors
59FF00
82FF00
B8FF75
E3FFCB
F4FFEA

Requirements
Must have
• Must have my company logo
Should not have
• No photos or complex graphics

```html
<!DOCTYPE html>
<html lang="en">
<head>
<meta charset="utf-8">
<title>Brookvale Building Company – Sign</title>
<link rel="stylesheet" href="https://fonts.googleapis.com/css2?family=Arimo:wght@400;700&family=Montserrat:wght@400;600&display=swap">
<style>
  :root {
    --stage: #3a3f4a;
    --board: #1e1e1e;
    --green: #62b83f;
    --white: #ffffff;
    --muted: #d9d9d9;
  }
  * { box-sizing: border-box; margin: 0; padding: 0; }
  html, body { width: 1200px; height: 800px; overflow: hidden; }
  body { background: var(--stage); position: relative; font-family: "Arimo", Arial, sans-serif; }

  .sign {
    position: absolute; left: 40px; top: 120px;
    width: 1120px; height: 560px;
    background: var(--board);
  }

  .brand {
    position: absolute; left: 0; right: 0; top: 96px;
    display: flex; flex-direction: column; align-items: center; gap: 10px;
    margin-left: 150px;
  }
  .brand-row { display: flex; align-items: center; gap: 12px; }
  .brand-square { width: 26px; height: 26px; background: var(--green); }
  .brand-name {
    font-family: "Arimo", Arial, sans-serif; font-weight: 700;
    font-size: 30px; color: var(--white); letter-spacing: 1px;
  }
  .brand-est {
    font-family: "Montserrat", Arial, sans-serif; font-size: 10px;
    letter-spacing: 3px; color: var(--muted);
  }

  .headline {
    position: absolute; left: 0; right: 0; top: 250px;
    text-align: center; margin-left: 150px; color: var(--green);
  }
  .headline-lead { font-family: "Arimo", Arial, sans-serif; font-weight: 700; font-size: 44px; letter-spacing: 1px; }
  .headline-main {
    font-family: "Montserrat", Arial, sans-serif; font-weight: 600;
    font-size: 84px; letter-spacing: 16px; line-height: 1; margin-top: 6px;
  }

  .contact {
    position: absolute; left: 136px; right: 60px; top: 446px;
    display: flex; align-items: center; gap: 64px;
  }
  .phone { display: flex; align-items: center; gap: 20px; }
  .phone-number { font-family: "Arimo", Arial, sans-serif; font-weight: 700; font-size: 46px; color: var(--white); }
  .online { display: flex; flex-direction: column; gap: 12px; }
  .online-item { display: flex; align-items: center; gap: 18px; font-family: "Montserrat", Arial, sans-serif; font-size: 19px; color: var(--white); }
  .icon { flex: none; }
</style>
</head>
<body>
  <main class="sign">
    <div class="brand">
      <div class="brand-row">
        <span class="brand-square"></span>
        <span class="brand-name">Brookvale Building Company</span>
      </div>
      <span class="brand-est">ESTD 2020</span>
    </div>

    <div class="headline">
      <p class="headline-lead">Build with the</p>
      <p class="headline-main">B-CREW!</p>
    </div>

    <div class="contact">
      <div class="phone">
        <svg class="icon" width="24" height="24" viewBox="0 0 24 24" aria-hidden="true">
          <path d="M6.6 10.8a15 15 0 0 0 6.6 6.6l2.2-2.2a1 1 0 0 1 1-.25 11.4 11.4 0 0 0 3.6.6 1 1 0 0 1 1 1V20a1 1 0 0 1-1 1A17 17 0 0 1 3 4a1 1 0 0 1 1-1h3.5a1 1 0 0 1 1 1c0 1.25.2 2.45.6 3.6a1 1 0 0 1-.25 1z" fill="var(--green)"/>
        </svg>
        <span class="phone-number">831-555-0172</span>
      </div>
      <div class="online">
        <div class="online-item">
          <svg class="icon" width="20" height="20" viewBox="0 0 20 20" aria-hidden="true" fill="none" stroke="var(--green)" stroke-width="1.6">
            <circle cx="10" cy="10" r="8"/><ellipse cx="10" cy="10" rx="3.6" ry="8"/><path d="M2 10h16M3.5 6h13M3.5 14h13"/>
          </svg>
          <span>BrookvaleBuildingCompany.example</span>
        </div>
        <div class="online-item">
          <svg class="icon" width="20" height="16" viewBox="0 0 20 16" aria-hidden="true">
            <rect x="1" y="1" width="18" height="14" fill="var(--green)"/>
            <path d="M1 1l9 7 9-7" fill="none" stroke="var(--board)" stroke-width="1.6"/>
          </svg>
          <span>brookvalebuildingcompany@mailnest.example</span>
        </div>
      </div>
    </div>
  </main>
</body>
</html>
```